Restaurant Menu New Design

Hello Designers,

Blue Fern is a casual family oriented dine-in restaurant, we serve American Italian dishes like Pizza, Pasta, and Sandwiches.

We are excited about adding some new delicious dishes and recipes to our menu. And we are looking for a talented and creative designer to design it.

The menu is a 12 page black leather book, page size is:
6.5" X 11.69" (16.51 cm X 29.69 cm)

Below is the scope of work and requirements:

1) Design a completely all new, creative, and beautiful menu, including cover page, blue fern oven intro. page, interior pages, and kids menu page.

2) Design a take out edition of the menu. It will be exactly the same as the dine-in menu, but with the addition of a back cover page with info such as contacts, social media, location map, etc…

3) Files are required in Adobe Illustrator format. Layers should be organized, all text should be editable, and all the food pictures easy to change.

4) This is a two language menu, so you are required to make space in the design for a second language. The easiest way to do that is have every item listed in English twice, then I will edit the second text with Illustrator.

5) In your initial design submission, the minimum you are required to submit are these 4 pages:
– Cover page
– Typical interior menu page
– Kids menu page
– Take-out menu back cover page

If your initial design is selected, then you are required to submit all remaining pages to complete the project.

In the link below, you will find:
1) Logo
2) New menu text in Excel
3) Food images (will take some time to upload)
4) The old dine-in and take out menu designs

https://www.filevaultra.com/sh/kq7tmwzabe3pxd/BBBrTnpLk41QaWmZpQ8V2X7Jd?dl=0

Thank you for stopping by and reading this brief. I hope you like this project and enjoy designing our new menu. Please let me know if you have any questions.

Cheers!

Project Deadline Extended
Reason: We have decided to extend the deadline due to the low number of submissions which was much lower than the expected submissions we were give by Brief Harbor.

```html
<!DOCTYPE html>
<html lang="en">
<head>
<meta charset="utf-8">
<title>Blue Fern — Sandwiches</title>
<link href="https://fonts.googleapis.com/css2?family=Lato:wght@400;700;900&family=Tajawal:wght@400;500&display=swap" rel="stylesheet">
<style>
  :root{
    --board:#333334;
    --ink:#ffffff;
    --body:#d9d9d9;
    --muted:#bdbdbd;
    --rule:#e6e6e6;
    --doodle:#4a4a4b;
    --photo-a:#8a5a34;
    --photo-b:#c9963f;
  }
  *{box-sizing:border-box;margin:0;padding:0}
  html,body{width:1200px;height:2166px;overflow:hidden;background:var(--board)}
  .menu-page{position:relative;width:1200px;height:2166px;background:var(--board);color:var(--ink);font-family:Arial, Helvetica, sans-serif}
  .section-title{position:absolute;top:64px;font-family:'Lato',sans-serif;font-weight:400;font-size:40px;letter-spacing:1px;color:var(--ink)}
  .section-title.left{left:214px}
  .section-title.right{left:755px}
  .rule{position:absolute;background:var(--rule)}
  .doodle{position:absolute;background:var(--doodle);border-radius:50%}
  .doodle.bar{border-radius:10px}
  .photo{position:absolute;top:832px;width:428px;height:284px;background:linear-gradient(135deg,var(--photo-a),var(--photo-b) 60%,#b8352c)}
  .item{position:absolute;width:420px;text-align:center}
  .item.left{left:98px}
  .item.right{left:674px}
  .item-name{font-family:'Lato',sans-serif;font-weight:900;font-size:26px;line-height:32px;color:var(--ink)}
  .item-name-ar{font-family:'Tajawal',sans-serif;font-weight:500;font-size:25px;line-height:32px;color:var(--ink)}
  .item-desc{font-size:17.5px;line-height:23px;color:var(--body);margin-top:14px}
  .item-desc-ar{font-family:'Tajawal',sans-serif;font-size:18px;line-height:24px;color:var(--muted);margin-top:14px;direction:rtl}
  .item-extra{font-size:17.5px;line-height:23px;color:var(--body);margin-top:14px}
  .wave{position:absolute;left:70px;top:1600px}
</style>
</head>
<body>
<main class="menu-page">

  <!-- Header -->
  <h1 class="section-title left">SANDWICHES</h1>
  <h1 class="section-title right">SANDWICHES</h1>
  <div class="rule" style="left:0;top:125px;width:202px;height:2px"></div>
  <div class="rule" style="left:997px;top:105px;width:203px;height:2px"></div>
  <div class="doodle bar" role="img" aria-label="Line drawing of a serving cloche" style="left:536px;top:66px;width:132px;height:88px"></div>
  <div class="doodle bar" role="img" aria-label="Line drawings of a spatula, chili and tomato" style="left:160px;top:146px;width:296px;height:36px"></div>
  <div class="doodle bar" role="img" aria-label="Line drawings of beetroot, carrot and spatula" style="left:752px;top:136px;width:260px;height:50px"></div>

  <!-- Top right frame -->
  <div class="rule" style="left:780px;top:243px;width:356px;height:2px"></div>
  <div class="rule" style="left:1134px;top:243px;width:2px;height:508px"></div>

  <!-- Column doodles -->
  <div class="doodle" role="img" aria-label="Line drawing of an onion" style="left:588px;top:206px;width:58px;height:74px"></div>
  <div class="doodle" role="img" aria-label="Line drawing of mushrooms" style="left:548px;top:366px;width:56px;height:54px"></div>
  <div class="doodle" role="img" aria-label="Line drawing of a pea pod" style="left:604px;top:478px;width:80px;height:44px"></div>
  <div class="doodle" role="img" aria-label="Line drawing of a pepper" style="left:572px;top:590px;width:40px;height:48px"></div>
  <div class="doodle" role="img" aria-label="Line drawing of an eggplant" style="left:882px;top:694px;width:70px;height:64px"></div>

  <!-- Cheese steak -->
  <article class="item left" style="top:234px">
    <h2 class="item-name">CHEESE STEAK |</h2>
    <p class="item-name-ar">ستيك بالجبنة</p>
    <p class="item-desc">Thinly sliced beef, sauteed onions &amp; mushrooms, cheddar cheese, ketchup, mayo, pickles&nbsp;&nbsp;39</p>
    <p class="item-desc-ar">شرائح اللحم البقري الخفيفة، سوتيه البصل و المشروم، جبنة تشيدر، كتشب، مايونيز، مخلل 39</p>
  </article>

  <!-- Grilled chicken -->
  <article class="item left" style="top:498px">
    <h2 class="item-name">GRILLED CHICKEN | <span class="item-name-ar">دجاج مشوي</span></h2>
    <p class="item-desc">Grilled chicken breast, lettuce, pickles, herb &amp; garlic mayo&nbsp;&nbsp;37</p>
    <p class="item-desc-ar">صدر دجاج مشوي، خس، مخلل ومايونيز بالثوم والأعشاب 37<br>أضف جبنة تشيدر أو جبنة سويسرية +3</p>
    <p class="item-extra">Add swiss or cheddar cheese&nbsp;&nbsp;+3</p>
  </article>

  <!-- Cowboy BBQ burger -->
  <article class="item right" style="top:304px">
    <h2 class="item-name">COWBOY BBQ BURGER |</h2>
    <p class="item-name-ar">كاوبوي باربيكيو برجر</p>
    <p class="item-desc" style="margin-top:32px">200 grams of pure Angus beef, flame broiled and served on freshly baked buns with beef bacon, melting cheddar cheese, crispy onion rings, BBQ sauce and mayonnaise&nbsp;&nbsp;44</p>
    <p class="item-desc-ar" style="margin-top:28px">200 غرام من لحم الأنجوس الصافي، مشوية على اللهب و مقدمة على خبز طازج مع شرائح البيكون و جبنة التشيدر السائحة، البصل المقرمش، و صوص الباربيكيو و المايونيز 44</p>
  </article>

  <!-- Middle divider -->
  <div class="rule" style="left:0;top:760px;width:1200px;height:2px"></div>
  <div class="doodle bar" role="img" aria-label="Line drawing of a rolling pin" style="left:462px;top:748px;width:280px;height:26px"></div>

  <!-- Photo frames -->
  <div class="rule" style="left:72px;top:799px;width:102px;height:2px"></div>
  <div class="rule" style="left:72px;top:799px;width:2px;height:248px"></div>
  <div class="rule" style="left:1131px;top:751px;width:2px;height:404px"></div>
  <div class="rule" style="left:1061px;top:1154px;width:72px;height:2px"></div>
  <div class="photo" role="img" aria-label="Photo of a crispy club sandwich with fries and coleslaw" style="left:111px"></div>
  <div class="photo" role="img" aria-label="Photo of a hot roast beef burger with fries and coleslaw" style="left:669px"></div>
  <div class="doodle" role="img" aria-label="Line drawing of mushrooms" style="left:570px;top:864px;width:54px;height:60px"></div>
  <div class="doodle" role="img" aria-label="Line drawing of a tomato" style="left:592px;top:1016px;width:48px;height:46px"></div>

  <!-- Crispy club -->
  <article class="item left" style="top:1178px;left:105px">
    <h2 class="item-name">CRISPY CLUB SANDWICH|</h2>
    <p class="item-name-ar">كرسبي كلوب ساندوتش</p>
    <p class="item-desc" style="margin-top:22px">Crispy fried chicken breast with bacon, swiss &amp; cheddar cheese, mayo, lettuce, tomatos, &amp; pickles&nbsp;&nbsp;39</p>
    <p class="item-desc-ar" style="margin-top:20px">صدر الدجاج المقلي المقرمش مع البيكون والجبنة السويسرية والشيدر والمايونيز والخس والطماطم والمخلل 39</p>
  </article>

  <!-- Hot roast beef -->
  <article class="item right" style="top:1178px;left:678px">
    <h2 class="item-name">HOT ROAST BEEF|</h2>
    <p class="item-name-ar">هوت روست بيف</p>
    <p class="item-desc" style="margin-top:22px">Thin slices of slow cooked roast beef, cheddar cheese, mayonaise, BBQ sauce, pickles&nbsp;&nbsp;37</p>
    <p class="item-desc-ar" style="margin-top:20px">شرائح لحم الروستو الساخنة مقدمة مع صوص الباربكيو والمايونيز والمخلل وجبنة التشدر السائحة 37</p>
  </article>
  <div class="rule" style="left:1140px;top:1271px;width:2px;height:205px"></div>
  <div class="rule" style="left:986px;top:1475px;width:156px;height:2px"></div>
  <div class="doodle" role="img" aria-label="Line drawing of a pomegranate" style="left:566px;top:1214px;width:76px;height:78px"></div>
  <div class="doodle" role="img" aria-label="Line drawing of an eggplant" style="left:530px;top:1418px;width:72px;height:66px"></div>
  <div class="rule" style="left:14px;top:1495px;width:470px;height:2px"></div>

  <!-- Mushroom & swiss -->
  <svg class="wave" width="40" height="330" viewBox="0 0 40 330" aria-hidden="true">
    <path d="M20 2 C40 40 36 70 18 110 C4 150 30 190 28 230 C26 270 8 300 26 328" fill="none" stroke="#e6e6e6" stroke-width="2"/>
  </svg>
  <article class="item left" style="top:1592px;left:116px">
    <h2 class="item-name">MUSHROOM &amp;<br>SWISS BURGER|</h2>
    <p class="item-name-ar">مشروم اند سويس برجر</p>
    <p class="item-desc" style="margin-top:22px;line-height:27px">200 grams of pure Angus beef, flame broiled and served on freshly baked buns with melting swiss cheese, sauteed mushrooms &amp; onions, and mayonnaise&nbsp;&nbsp;42</p>
    <p class="item-desc-ar" style="margin-top:20px">200 غرام من لحم الأنجوس الصافي، مشوية على اللهب و مقدمة على خبز طازج مع الجبنة السويسرية السائحة، البصل و المشروم، و المايونيز 42</p>
  </article>
  <div class="doodle" role="img" aria-label="Line drawing of a cheese wedge" style="left:590px;top:1522px;width:64px;height:74px"></div>
  <div class="doodle" role="img" aria-label="Line drawing of a mushroom" style="left:550px;top:1660px;width:76px;height:74px"></div>
  <div class="doodle" role="img" aria-label="Line drawing of a rosemary sprig" style="left:540px;top:1836px;width:80px;height:80px"></div>

  <!-- Cheeseburger -->
  <article class="item right" style="top:1540px;left:672px;width:440px">
    <h2 class="item-name">CHEESEBURGER | <span class="item-name-ar">تشيزبرجر</span></h2>
    <p class="item-desc" style="margin-top:26px">200 grams of pure Angus beef, flame broiled and served on freshly baked buns with cheddar cheese, lettuce, tomatos, onions, pickles, and special sauce&nbsp;&nbsp;39</p>
    <p class="item-desc-ar" style="margin-top:18px">200 غرام من لحم الأنجوس الصافي، مشوية على اللهب و مقدمة على خبز طازج مع جبنة تشيدر، خس، طماطم، بصل، مخلل، و الصوص المميز 39</p>
  </article>

  <!-- Fried shrimp -->
  <article class="item right" style="top:1858px;left:672px;width:440px">
    <h2 class="item-name">FRIED SHRIMP | <span class="item-name-ar">جمبري مقلي</span></h2>
    <p class="item-desc" style="margin-top:26px">Breaded shrimp, lettuce, pickles, cocktail sauce&nbsp;&nbsp;42</p>
    <p class="item-desc-ar" style="margin-top:18px">جمبري مقلي، خس، مخلل وصوص كوكتيل 42</p>
  </article>

  <!-- Bottom divider -->
  <div class="rule" style="left:0;top:2075px;width:1200px;height:2px"></div>
  <div class="doodle bar" role="img" aria-label="Line drawing of a rolling pin" style="left:462px;top:2063px;width:280px;height:26px"></div>

</main>
</body>
</html>
```